Amber Vital 480

This is a 9 week program we conduct in our gym/recovery facility with the aim of educating members on the ins and outs of training, sauna use, cold plunge, sleep and lifestyle factors that they need to consider to increase health span into their older age. It is geared towards the Gen X age group.

```html
<!DOCTYPE html>
<html lang="en">
<head>
<meta charset="utf-8">
<title>Amber Vital 480</title>
<link href="https://fonts.googleapis.com/css2?family=Outfit:wght@300;400;500;600;700&display=swap" rel="stylesheet">
<style>
:root{
  --navy:#0b2a78;
  --blue:#1655b3;
  --sky:#1e9ad6;
  --ink:#111826;
  --muted:#5b6270;
  --pale:#dbe9f7;
  --white:#ffffff;
  --black:#070707;
}
*{margin:0;padding:0;box-sizing:border-box}
html,body{width:1200px;height:3549px;overflow:hidden}
body{font-family:'Outfit',sans-serif;color:var(--ink);background:var(--white);position:relative}
.abs{position:absolute}
.brand{display:flex;align-items:center;gap:12px;font-weight:700;color:var(--navy);font-size:22px}
.brand-dot{width:48px;height:48px;border-radius:50%;background:var(--blue)}
/* header */
.site-header{position:absolute;top:0;left:0;width:1200px;height:100px}
.site-header .brand{position:absolute;left:80px;top:26px}
.main-nav{position:absolute;left:384px;top:40px;display:flex;gap:34px;font-size:15px;color:#222}
.main-nav .active{color:var(--navy);font-weight:500}
.call{position:absolute;left:888px;top:28px;display:flex;align-items:center;gap:18px}
.call-icon{width:44px;height:44px;border-radius:50%;background:var(--navy);display:flex;align-items:center;justify-content:center}
.call small{display:block;font-size:11px;color:#222}
.call strong{font-size:21px;color:var(--navy);font-weight:600}
/* hero */
.hero{top:100px;left:0;width:1200px;height:469px;background:linear-gradient(90deg,#2a2a22 0%,#3c4331 30%,#8a8f72 55%,#c8b39a 75%,#a89580 100%)}
.hero::after{content:"";position:absolute;inset:0;background:linear-gradient(90deg,rgba(0,0,0,.45),rgba(0,0,0,0) 55%)}
.hero-text{position:absolute;left:110px;top:110px;color:var(--white);z-index:2}
.hero-text h3{font-size:30px;font-weight:600;letter-spacing:.5px}
.hero-text h1{font-size:58px;font-weight:600;line-height:1.1;margin-top:4px}
.hero-text p{font-size:16px;line-height:30px;width:430px;margin-top:12px}
.btn{display:inline-flex;align-items:center;gap:10px;height:40px;padding:0 20px 0 5px;border-radius:20px;background:linear-gradient(90deg,var(--sky),var(--navy));color:var(--white);font-size:15px;font-weight:600}
.btn i{width:32px;height:32px;border-radius:50%;background:var(--white);display:block;border:6px solid var(--sky)}
.hero-text .btn{margin-top:24px}
.scroll-notch{position:absolute;left:563px;top:540px;width:74px;height:60px;border-radius:37px 37px 0 0;background:var(--white);z-index:3;display:flex;justify-content:center;padding-top:12px}
/* headings */
.sec-title{position:absolute;left:0;width:1200px;text-align:center}
.sec-title h2{font-size:41px;font-weight:500}
.sec-title p{font-size:17px;color:var(--muted);margin-top:14px}
/* program */
.card{position:absolute;top:742px;width:313px;height:410px;background:var(--white);border-radius:18px;box-shadow:0 4px 18px rgba(20,40,90,.09);padding:11px}
.card .photo{height:223px;border-radius:18px;position:relative}
.tag{position:absolute;left:18px;top:18px;background:var(--navy);color:var(--white);font-size:14px;padding:6px 18px;border-radius:16px}
.meta{display:flex;gap:10px;margin:24px 0 0 14px}
.meta span{font-size:12px;padding:7px 14px;border-radius:16px;background:var(--pale);color:var(--blue)}
.meta span.time{background:#cfd6e4;color:#222}
.card h4{font-size:18px;font-weight:500;margin:18px 0 0 14px}
.card p{font-size:13.5px;color:var(--muted);line-height:25px;margin:10px 14px 0}
.pager{position:absolute;left:559px;display:flex;gap:11px}
.pager span{width:34px;height:34px;border-radius:50%;background:var(--pale);color:var(--blue);display:flex;align-items:center;justify-content:center;font-size:16px}
/* about */
.about-circle{left:115px;top:1250px;width:430px;height:430px;border-radius:50%;background:radial-gradient(circle at 45% 45%,#e9d3c0,#b99a84 60%,#6a5a50)}
.about-accent{left:520px;top:1448px;width:62px;height:62px;border-radius:50%;background:var(--sky)}
.about-small{left:376px;top:1472px;width:234px;height:234px;border-radius:50%;border:6px solid var(--white);background:linear-gradient(160deg,#f0d7a8,#c9b08a 55%,#6f8a5a);box-shadow:0 8px 20px rgba(0,0,0,.15)}
.text-block{position:absolute;width:420px}
.text-block h2{font-size:41px;font-weight:500}
.text-block p{font-size:14.5px;color:var(--muted);line-height:30px;margin-top:14px}
.text-block .btn{margin-top:22px}
/* customers */
.band{left:0;top:1778px;width:1200px;height:527px}
.band-title{top:1845px;color:var(--white)}
.band-title p{color:var(--white)}
.review{position:absolute;top:1980px;width:475px;height:187px;background:var(--white);border-radius:94px}
.review .avatar{position:absolute;left:-1px;top:25px;width:140px;height:140px;border-radius:50%;background:linear-gradient(140deg,#8aa37a,#3f5a3a);border:5px solid var(--white)}
.review p{position:absolute;left:165px;top:32px;width:275px;font-size:13.5px;line-height:25px;color:var(--muted)}
.review strong{position:absolute;left:165px;top:140px;font-size:16px;color:var(--navy);font-weight:600}
.review .quote{position:absolute;right:26px;top:110px;font-size:100px;line-height:1;color:#d0d3d8;font-weight:700}
.band-pager span{background:rgba(10,40,110,.5);color:var(--white)}
/* why */
.why{position:absolute;top:2480px;width:186px;height:175px;background:var(--white);border-radius:18px;box-shadow:0 4px 18px rgba(20,40,90,.09);text-align:center;padding-top:32px;font-size:15px}
.why .ic{width:66px;height:66px;border-radius:50%;background:linear-gradient(160deg,var(--sky),var(--navy));margin:0 auto 20px;display:flex;align-items:center;justify-content:center}
/* resources */
.res-circle{left:965px;top:2970px;width:206px;height:206px;border-radius:50%;background:linear-gradient(160deg,var(--navy),var(--sky))}
.res-photo{left:600px;top:2755px;width:488px;height:370px;border-radius:22px;background:linear-gradient(120deg,#e7e2da,#cfc4b8 45%,#e6a8b8 60%,#7b7f86)}
/* footer */
.footer{left:0;top:3238px;width:1200px;height:311px;background:var(--black);color:var(--white)}
.footer .brand{color:var(--white);font-size:30px;justify-content:center;position:absolute;left:0;width:1200px;top:70px}
.footer .brand-dot{width:60px;height:60px;background:var(--white)}
.foot-nav{position:absolute;top:177px;left:0;width:1200px;display:flex;justify-content:center;gap:46px;font-size:15px}
.social{position:absolute;top:217px;left:0;width:1200px;display:flex;justify-content:center;gap:8px}
.social span{width:36px;height:36px;border-radius:50%;background:var(--blue)}
.copy{position:absolute;top:273px;left:0;width:1200px;text-align:center;font-size:14px}
</style>
</head>
<body>

<header class="site-header">
  <div class="brand"><span class="brand-dot"></span>Amber Vital 480</div>
  <nav class="main-nav">
    <span class="active">Home</span><span>About Us</span><span>Our Programs</span><span>Reviews</span><span>Contact Us</span>
  </nav>
  <div class="call">
    <div class="call-icon"><svg width="18" height="18" viewBox="0 0 24 24"><path fill="#fff" d="M6.6 10.8a15 15 0 0 0 6.6 6.6l2.2-2.2c.3-.3.7-.4 1-.2 1.1.4 2.3.6 3.6.6.6 0 1 .4 1 1V20c0 .6-.4 1-1 1A17 17 0 0 1 3 4c0-.6.4-1 1-1h3.5c.6 0 1 .4 1 1 0 1.3.2 2.5.6 3.6.1.3 0 .7-.2 1z"/></svg></div>
    <div><small>Call Us:</small><strong>+1 555 010 4800</strong></div>
  </div>
</header>

<section class="hero abs" role="img" aria-label="Smiling older women laughing together outdoors">
  <div class="hero-text">
    <h3>WELCOME TO</h3>
    <h1>Amber Vital 480</h1>
    <p>Quis nostrud exercitation ullamco laboris nisi ut aliquip ex ea commodo consequat duis aute irure.</p>
    <span class="btn"><i></i>Join With Us</span>
  </div>
</section>
<div class="scroll-notch"><svg width="16" height="26" viewBox="0 0 16 26"><rect x="1" y="1" width="14" height="24" rx="7" fill="#9aa0a8"/><path d="M8 7v10M5 14l3 3 3-3" stroke="#fff" stroke-width="1.6" fill="none"/></svg></div>

<div class="sec-title" style="top:628px"><h2>Our 9 Week Program</h2><p>Quis nostrud exercitation ullamco laboris nisi ut aliquip ex ea commodo consequat. Duis aute</p></div>

<article class="card" style="left:110px">
  <div class="photo" role="img" aria-label="Seniors playing a board game with a caregiver" style="background:linear-gradient(150deg,#c9c3b8,#8a8f8a 50%,#5a6b80)"><span class="tag">Week 1</span></div>
  <div class="meta"><span>&#9679; By Coach Lee</span><span class="time">&#9719; 90 Mins</span></div>
  <h4>Eiusmod Tempor Incididunt</h4>
  <p>Excepteur sint occaecat cupidatat non pr o ident, sunt in culpa qui officia</p>
</article>
<article class="card" style="left:443px">
  <div class="photo" role="img" aria-label="Group of seniors dancing on a lawn" style="background:linear-gradient(170deg,#d8e0e6,#9fae8a 55%,#5f7a45)"><span class="tag">Week 2</span></div>
  <div class="meta"><span>&#9679; By Coach Lee</span><span class="time">&#9719; 90 Mins</span></div>
  <h4>Voluptatem Accusa Dolorem</h4>
  <p>Excepteur sint occaecat cupidatat non pr o ident, sunt in culpa qui officia</p>
</article>
<article class="card" style="left:776px">
  <div class="photo" role="img" aria-label="Caregivers assisting an elderly woman in a garden" style="background:linear-gradient(150deg,#b9c7a4,#7f9a6a 50%,#8f8a80)"><span class="tag">Week 3</span></div>
  <div class="meta"><span>&#9679; By Coach Lee</span><span class="time">&#9719; 90 Mins</span></div>
  <h4>Quis Autem Vel Eum Iure Repreh</h4>
  <p>Excepteur sint occaecat cupidatat non pr o ident, sunt in culpa qui officia</p>
</article>
<div class="pager" style="top:1184px"><span>&laquo;</span><span>&raquo;</span></div>

<div class="about-accent abs"></div>
<div class="about-circle abs" role="img" aria-label="Group of smiling older women close together"></div>
<div class="about-small abs" role="img" aria-label="Seniors dancing outdoors in autumn"></div>
<div class="text-block" style="left:668px;top:1292px">
  <h2>About Us</h2>
  <p>Sed ut perspiciatis unde omnis iste natus error sit voluptatem accusantium doloremque laudantium, totam rem aperiam, eaque ipsa quae ab illo inventore veritatis et quasi architecto beatae vitae dicta sunt explicabo.</p>
  <p>Neque porro quisquam est, qui dolorem ipsum quia dolor sit amet, consectetur, adipisci velit, sed quia non numquam eius modi tempora incidunt ut labore</p>
  <span class="btn"><i></i>Read More</span>
</div>

<svg class="band abs" width="1200" height="527" viewBox="0 0 1200 527" role="img" aria-label="Blue band over a photo of seniors walking in a park">
  <defs><linearGradient id="bandFill" x1="0" y1="0" x2="0" y2="1"><stop offset="0" stop-color="#0a2a80"/><stop offset=".55" stop-color="#1250a8"/><stop offset="1" stop-color="#1e96d2"/></linearGradient></defs>
  <path d="M0 90 Q600 -80 1200 90 L1200 450 Q600 600 0 450 Z" fill="url(#bandFill)"/>
</svg>
<div class="sec-title band-title"><h2>Our Happy Customers</h2><p>Quis nostrud exercitation ullamco laboris nisi ut aliquip ex ea commodo consequat. Duis aute</p></div>
<div class="review" style="left:112px">
  <div class="avatar" role="img" aria-label="Portrait of an older man on a scooter"></div>
  <p>Sed ut perspiciatis unde omnis iste natus error sit voluptatem accusantium dolor eque laudantium, totam rem aperiam, eaque ipsa quae ab illo inventore veritatis</p>
  <strong>Daniel Reyes</strong><span class="quote">&ldquo;</span>
</div>
<div class="review" style="left:614px">
  <div class="avatar" role="img" aria-label="Portrait of an older woman with headphones" style="background:linear-gradient(140deg,#e8e2d8,#b8aa98)"></div>
  <p>Sed ut perspiciatis unde omnis iste natus error sit voluptatem accusantium dolor eque laudantium, totam rem aperiam, eaque ipsa quae ab illo inventore veritatis</p>
  <strong>Priya Nair</strong><span class="quote">&ldquo;</span>
</div>
<div class="pager band-pager" style="top:2195px"><span>&laquo;</span><span>&raquo;</span></div>

<div class="sec-title" style="top:2362px"><h2>Why Choose Us</h2><p>Quis nostrud exercitation ullamco laboris nisi ut aliquip ex ea commodo consequat.</p></div>
<div class="why" style="left:100px"><div class="ic"><svg width="30" height="30" viewBox="0 0 30 30" fill="none" stroke="#fff" stroke-width="2"><path d="M4 15h22M8 10v10M22 10v10"/></svg></div>Ins &amp; Outs of Training</div>
<div class="why" style="left:304px"><div class="ic"><svg width="30" height="30" viewBox="0 0 30 30" fill="none" stroke="#fff" stroke-width="2"><path d="M6 14h18l-2 11H8zM11 5q2 3 0 6M16 5q2 3 0 6M21 5q2 3 0 6"/></svg></div>Sauna Use</div>
<div class="why" style="left:507px"><div class="ic"><svg width="30" height="30" viewBox="0 0 30 30" fill="none" stroke="#fff" stroke-width="2"><rect x="8" y="9" width="10" height="17" rx="2"/><path d="M11 5h4v4M20 16h5v10h-5"/></svg></div>Cold Plunge</div>
<div class="why" style="left:710px"><div class="ic"><svg width="30" height="30" viewBox="0 0 30 30" fill="none" stroke="#fff" stroke-width="2"><path d="M15 25S4 18 4 11a5 5 0 0 1 11-2 5 5 0 0 1 11 2c0 7-11 14-11 14z"/><path d="M7 14h5l2-3 3 6 2-3h4"/></svg></div>Increase Health Span</div>
<div class="why" style="left:913px"><div class="ic"><svg width="30" height="30" viewBox="0 0 30 30" fill="none" stroke="#fff" stroke-width="2"><rect x="4" y="14" width="22" height="7" rx="3.5"/><path d="M17 5h4l-4 4h4M22 9h3l-3 3h3"/></svg></div>Sleep &amp; Lifestyle</div>

<div class="res-circle abs"></div>
<div class="res-photo abs" role="img" aria-label="Older women doing a fitness class in a gym"></div>
<div class="text-block" style="left:115px;top:2755px;width:415px">
  <h2>Resources</h2>
  <p>Sed ut perspiciatis unde omnis iste natus error sit voluptatem accusantium doloremque laudantium, totam rem aperiam, eaque ipsa quae ab illo inventore veritatis et quasi architecto beatae vitae dicta sunt explicabo.</p>
  <p>Neque porro quisquam est, qui dolorem ipsum quia dolor sit amet, consectetur, adipisci velit, sed quia non numquam eius modi tempora incidunt ut labore</p>
  <span class="btn"><i></i>Read More</span>
</div>

<footer class="footer abs">
  <div class="brand"><span class="brand-dot"></span>Amber Vital 480</div>
  <nav class="foot-nav"><span>HOME</span><span>|</span><span>ABOUT US</span><span>|</span><span>OUR PROGRAMS</span><span>|</span><span>REVIEWS</span><span>|</span><span>CONTACT US</span></nav>
  <div class="social"><span></span><span></span><span></span></div>
  <p class="copy">(C) Copyright 2024 | All Rights Reserved</p>
</footer>

</body>
</html>
```